Business card for medical clinic

I need an upmarket, modern medical/health business card for my clinic

Contact Information for Business Card

name, address, email, qr code

```html
<!DOCTYPE html>
<html lang="en">
<head>
<meta charset="utf-8">
<title>Meridian Care Group – Business Card</title>
<link href="https://fonts.googleapis.com/css2?family=Montserrat:wght@400;500;700&display=swap" rel="stylesheet">
<style>
  :root {
    --page-bg: #1e1f23;
    --navy: #1f2b49;
    --navy-mid: #2a4a6e;
    --sky: #29a6de;
    --brand-blue: #1f6fa8;
    --ink: #1b1d24;
    --card-white: #ffffff;
  }
  * { margin: 0; padding: 0; box-sizing: border-box; }
  html, body {
    width: 1200px; height: 900px; overflow: hidden;
    background: var(--page-bg);
    font-family: "Montserrat", Arial, sans-serif;
  }
  .stage {
    width: 1200px; height: 900px;
    display: flex; flex-direction: column; align-items: center; justify-content: center;
    gap: 36px;
  }
  .card {
    position: relative;
    width: 700px; height: 400px;
    overflow: hidden;
  }
  /* Front side */
  .card-front {
    background: linear-gradient(30deg, var(--navy) 0%, var(--navy-mid) 45%, var(--sky) 100%);
    display: flex; align-items: center; justify-content: center;
  }
  .brand {
    display: flex; align-items: center; gap: 18px;
    font-weight: 500; letter-spacing: 0.12em; text-transform: uppercase;
    white-space: nowrap;
  }
  .brand-dot {
    border-radius: 50%;
    border: 3px solid currentColor;
    flex: none;
  }
  .card-front .brand { color: var(--card-white); font-size: 34px; }
  .card-front .brand-dot { width: 70px; height: 70px; }

  /* Back side */
  .card-back { background: var(--card-white); }
  .card-back .brand {
    position: absolute; left: 48px; top: 188px;
    width: 300px;
    color: var(--brand-blue); font-size: 15px; gap: 12px; letter-spacing: 0.1em;
  }
  .card-back .brand-dot { width: 40px; height: 40px; border-width: 2.5px; }
  .divider {
    position: absolute; left: 382px; top: 68px;
    width: 1.5px; height: 228px; background: var(--sky);
  }
  .contact {
    position: absolute; left: 408px; top: 70px;
    width: 270px;
    color: var(--ink);
  }
  .contact-name { font-size: 27px; font-weight: 700; color: var(--brand-blue); line-height: 1.1; }
  .contact-role { font-size: 14px; font-weight: 500; margin-top: 2px; }
  .contact-address { font-size: 14px; font-weight: 500; margin-top: 22px; line-height: 1.35; }
  .contact-lines { list-style: none; margin-top: 18px; font-size: 14px; font-weight: 500; }
  .contact-lines li { display: flex; align-items: center; gap: 10px; margin-bottom: 7px; }
  .contact-lines svg { width: 14px; height: 14px; flex: none; }
  .edge-bands { position: absolute; left: 0; bottom: 0; width: 700px; height: 60px; }
</style>
</head>
<body>
<main class="stage">

  <section class="card card-front" aria-label="Card front">
    <div class="brand"><span class="brand-dot"></span><span>Meridian Care Group</span></div>
  </section>

  <section class="card card-back" aria-label="Card back">
    <div class="brand"><span class="brand-dot"></span><span>Meridian Care Group</span></div>
    <div class="divider"></div>
    <div class="contact">
      <p class="contact-name">Daniel Hart</p>
      <p class="contact-role">Managing Director</p>
      <p class="contact-address">240 Cedar Hollow Road<br>Brookfield, MS 39045</p>
      <ul class="contact-lines">
        <li>
          <svg viewBox="0 0 16 16" aria-hidden="true"><path fill="#29a6de" d="M3.5 1.5l2.5 0 1 3.5-1.6 1.2a8 8 0 0 0 4.4 4.4L11 9l3.5 1v2.5c0 1-1 2-2 2C6.5 14.5 1.5 9.5 1.5 3.5c0-1 1-2 2-2z"/></svg>
          <span>555.014.2290</span>
        </li>
        <li>
          <svg viewBox="0 0 16 16" aria-hidden="true"><rect x="1" y="3" width="14" height="10" rx="1" fill="#29a6de"/><path d="M1.5 3.8L8 9l6.5-5.2" fill="none" stroke="#fff" stroke-width="1.3"/></svg>
          <span>info@meridiancare.com</span>
        </li>
        <li>
          <svg viewBox="0 0 16 16" aria-hidden="true"><circle cx="8" cy="8" r="6.5" fill="none" stroke="#29a6de" stroke-width="1.5"/><ellipse cx="8" cy="8" rx="2.6" ry="6.5" fill="none" stroke="#29a6de" stroke-width="1.3"/><path d="M1.5 8h13" stroke="#29a6de" stroke-width="1.3"/></svg>
          <span>www.meridiancare.com</span>
        </li>
      </ul>
    </div>
    <svg class="edge-bands" viewBox="0 0 700 60" aria-hidden="true">
      <polygon points="0,46 520,46 534,14 548,14 528,60 0,60" fill="#1f2b49"/>
      <polygon points="560,34 700,0 700,60 540,60" fill="#29a6de"/>
    </svg>
  </section>

</main>
</body>
</html>
```